FernPath....... a dash of Glow

I need a web design for a new business based in London that will be mobile (offered at homes, parks or a local cafe ect) called FernPath. I offer Life Coaching/Counselling sessions, Personal training, Massage and Sports Massage. Sessions range from an hour to half and hour. My aim is to help people along their journey to help give them gain clarity of where there going, helping them to towards their goals, so that can experience bliss. My website should represent a place people can come to release their stress and worries so that they leave feeling lighter, clearer and happier. I would like my website to reflect someone feeling ALIVE. I would also like a logo design for FernPath with a sentence underneath or near saying A dash of Glow.

Target Market(s)

middle class people

Industry/Entity Type

Business

Coding

Coded - Design and coding required

Number of Pages Required

4 page

Requirements
Must have
• 1st page About us
• 2nd page Services
• 3rd page Prices
• 4th page contact details
Nice to have
• mixture of cultures in images

```html
<!DOCTYPE html>
<html lang="en">
<head>
<meta charset="utf-8">
<title>FernPath — A dash of Glow</title>
<link href="https://fonts.googleapis.com/css2?family=Lato:wght@400;700;900&family=PT+Sans:ital,wght@0,400;0,700;1,400&display=swap" rel="stylesheet">
<style>
:root{
  --orange:#ef5f3c;
  --amber:#f3b21c;
  --gold:#e5b813;
  --olive:#6b5a1a;
  --olive-soft:#a8994d;
  --ink:#3c3c3c;
  --muted:#8a8a8a;
  --nav:#555;
  --footer:#1d1d1d;
  --top-line:#4a0c0c;
  --icon-fill:#fdebd9;
  --white:#fff;
}
*{margin:0;padding:0;box-sizing:border-box}
html,body{width:762px;height:1200px;overflow:hidden;background:var(--white)}
body{position:relative;font-family:"PT Sans",sans-serif;color:var(--ink)}
.abs{position:absolute}

.top-line{left:0;top:0;width:762px;height:3px;background:var(--top-line)}
.brand{left:54px;top:14px;width:90px;text-align:center}
.brand-dot{display:block;width:10px;height:10px;border-radius:50%;background:var(--orange);margin:0 auto 12px}
.brand-name{font-family:"Lato",sans-serif;font-size:16px;color:var(--olive);line-height:1}
.brand-tag{font-family:"Lato",sans-serif;font-size:8.5px;color:var(--olive-soft);margin-top:3px}
.login{left:630px;top:13px;width:69px;height:20px;background:linear-gradient(var(--amber),var(--gold));color:var(--white);font-family:"Lato",sans-serif;font-size:8.5px;display:flex;align-items:center;justify-content:center;gap:5px;border-radius:1px}
.nav{top:46px;left:318px;font-family:"Lato",sans-serif;font-size:8.5px;color:var(--nav)}
.nav a{color:inherit;text-decoration:none;position:absolute;white-space:nowrap}
.nav a.active{color:var(--orange)}
.nav a.active::after{content:"";position:absolute;left:-1px;right:-1px;top:13px;height:2px;background:var(--orange)}
.search{left:688px;top:48px}

.hero{left:0;top:84px;width:762px;height:304px;background:
  radial-gradient(ellipse at 75% 35%,#f3ede2 0%,rgba(240,225,200,.6) 25%,transparent 50%),
  radial-gradient(ellipse at 30% 55%,#5a4632 0%,#6b4f30 18%,transparent 40%),
  linear-gradient(110deg,#e89a17 0%,#f0b534 30%,#e9a52a 55%,#d38a1d 100%)}
.hero-shadow{left:30px;top:386px;width:702px;height:10px;border-radius:50%;box-shadow:0 6px 8px rgba(0,0,0,.18)}
.hero-title{left:440px;top:150px;width:270px;text-align:right;font-family:"Lato",sans-serif;font-weight:900;font-size:47px;color:var(--white);text-shadow:2px 2px 3px rgba(0,0,0,.35);letter-spacing:.5px}
.hero-tag{left:440px;top:206px;width:252px;text-align:right;font-family:"Lato",sans-serif;font-size:16px;color:var(--white);letter-spacing:9px}

.section-title{left:0;width:762px;text-align:center;font-family:"Lato",sans-serif;font-weight:400;font-size:21px;line-height:26px;color:transparent;background-image:linear-gradient(90deg,var(--orange) 0 380px,var(--amber) 400px);-webkit-background-clip:text;background-clip:text}
.section-title.welcome{background-image:linear-gradient(90deg,var(--orange) 0 392px,var(--amber) 400px)}
.section-sub{left:0;width:762px;text-align:center;font-style:italic;font-size:8px;color:var(--muted)}

.service{width:160px;text-align:center}
.service-icon{display:block;margin:0 auto}
.service-name{font-family:"Lato",sans-serif;font-size:10.5px;color:var(--orange);margin-top:9px}
.service-text{font-size:7.2px;line-height:13px;color:var(--muted);margin-top:4px}
.slider-arrow{top:520px}

.about{left:0;top:651px;width:762px;height:204px;background:
  radial-gradient(ellipse at 30% 60%,#6e5042 0%,transparent 55%),
  linear-gradient(90deg,#7a6053 0%,#8c7062 45%,#a08777 75%,#b8a497 100%)}
.about-title{left:0;top:682px;width:762px;text-align:center;font-family:"Lato",sans-serif;font-weight:400;font-size:21px;color:var(--white)}
.about-text{left:118px;top:714px;width:526px;text-align:center;font-size:7.3px;line-height:15px;color:#f3ece6}
.read-more{left:338px;top:786px;width:87px;height:21px;background:linear-gradient(var(--amber),var(--gold));color:var(--white);font-size:8px;display:flex;align-items:center;justify-content:center;box-shadow:0 1px 2px rgba(0,0,0,.3)}

.event{width:140px}
.event-title{font-size:10.3px;color:var(--ink)}
.event-meta{font-size:7.5px;color:var(--muted);margin-top:8px;display:flex;align-items:center;gap:6px}
.event.left{text-align:right}
.event.left .event-meta{justify-content:flex-end}
.date{width:48px;height:48px;border-radius:50%;border:1.5px solid var(--amber);text-align:center;font-family:"Lato",sans-serif}
.date b{display:block;font-size:10px;color:var(--ink);font-weight:700}
.date span{display:block;font-size:8px;color:var(--ink);margin-top:9px}
.center-brand{left:311px;top:1010px;width:140px;text-align:center}
.center-brand .brand-dot{width:8px;height:8px;margin-bottom:14px}
.center-brand .brand-name{font-size:20px}
.center-brand .brand-tag{font-size:11px;margin-top:4px}

.footer{left:0;top:1129px;width:762px;height:71px;background:var(--footer)}
.footer-links{left:0;top:1153px;width:762px;text-align:center;font-size:8px;color:#e6e6e6;word-spacing:1px}
.footer-copy{left:0;top:1169px;width:762px;text-align:center;font-size:7.5px;color:#e6e6e6}
.social{left:605px;top:1155px;display:flex;gap:4px}
.social i{width:16px;height:16px;border:1px solid #e6e6e6;border-radius:50%;display:block}
</style>
</head>
<body>
<div class="abs top-line"></div>

<header>
  <div class="abs brand">
    <span class="brand-dot"></span>
    <div class="brand-name">FernPath</div>
    <div class="brand-tag">A dash of Glow</div>
  </div>
  <div class="abs login">
    <svg width="8" height="8" viewBox="0 0 10 10"><path d="M1 4h4V2l3 3-3 3V6H1z" fill="#fff"/><path d="M6 1h3v8H6" fill="none" stroke="#fff" stroke-width="1"/></svg>
    Log In
  </div>
  <nav class="abs nav">
    <a class="active" style="left:0">Home</a>
    <a style="left:50px">About Us</a>
    <a style="left:116px">Services</a>
    <a style="left:175px">Our Aim</a>
    <a style="left:237px">Testimonials</a>
    <a style="left:313px">Contacts</a>
  </nav>
  <svg class="abs search" width="10" height="10" viewBox="0 0 10 10"><circle cx="4" cy="4" r="3" fill="none" stroke="#ef5f3c" stroke-width="1.5"/><path d="M6.2 6.2 9 9" stroke="#ef5f3c" stroke-width="1.7"/></svg>
</header>

<div class="abs hero" role="img" aria-label="Photo of a joyful woman with arms outstretched among golden autumn trees"></div>
<div class="abs hero-shadow"></div>
<div class="abs hero-title">FERNPATH</div>
<div class="abs hero-tag">A dash of Glow</div>

<h2 class="abs section-title welcome" style="top:412px">Welcome to FernPath</h2>
<p class="abs section-sub" style="top:445px">Nemo enim ipsam voluptatem quia voluptas sit aspernatur aut odit aut fugit, sed quia consequuntur</p>

<svg class="abs slider-arrow" style="left:62px" width="12" height="34" viewBox="0 0 12 34"><path d="M11 1 1 17l10 16" fill="none" stroke="#ddd"/></svg>
<svg class="abs slider-arrow" style="left:688px" width="12" height="34" viewBox="0 0 12 34"><path d="M1 1l10 16L1 33" fill="none" stroke="#ddd"/></svg>

<svg width="0" height="0" class="abs"><defs>
  <linearGradient id="ring" x1="0" y1="0" x2="1" y2="1"><stop offset="0" stop-color="#ef5f3c"/><stop offset="1" stop-color="#f3b21c"/></linearGradient>
  <radialGradient id="iconFill"><stop offset="0" stop-color="#fbd9b0"/><stop offset="1" stop-color="#fdf1e4"/></radialGradient>
</defs></svg>

<div class="abs service" style="left:114px;top:485px">
  <svg class="service-icon" width="68" height="68" viewBox="0 0 68 68"><circle cx="34" cy="34" r="33" fill="none" stroke="url(#ring)" stroke-width="1.3"/><circle cx="34" cy="34" r="22" fill="url(#iconFill)" role="img" aria-label="Icon of a life coach"/></svg>
  <div class="service-name">Life Coaching</div>
  <p class="service-text">Nemo enim ipsam voluptatem quia sit aspernatur aut odit aut fugit, sed quia magni dolores eos qui ratione voluptatem</p>
</div>
<div class="abs service" style="left:301px;top:485px">
  <svg class="service-icon" width="68" height="68" viewBox="0 0 68 68"><circle cx="34" cy="34" r="33" fill="none" stroke="url(#ring)" stroke-width="1.3"/><circle cx="34" cy="34" r="22" fill="url(#iconFill)" role="img" aria-label="Icon of a figure in a yoga pose"/></svg>
  <div class="service-name">Personal training</div>
  <p class="service-text">Nemo enim ipsam voluptatem quia sit aspernatur aut odit aut fugit, sed quia magni dolores eos qui ratione voluptatem</p>
</div>
<div class="abs service" style="left:496px;top:485px">
  <svg class="service-icon" width="68" height="68" viewBox="0 0 68 68"><circle cx="34" cy="34" r="33" fill="none" stroke="url(#ring)" stroke-width="1.3"/><circle cx="34" cy="34" r="22" fill="url(#iconFill)" role="img" aria-label="Icon of stacked massage stones"/></svg>
  <div class="service-name">Massage and Sports Massage</div>
  <p class="service-text">Nemo enim ipsam voluptatem quia sit aspernatur aut odit aut fugit, sed quia magni dolores eos ...</p>
</div>

<section>
  <div class="abs about" role="img" aria-label="Soft photo of a relaxing facial massage"></div>
  <h2 class="abs about-title">About Us</h2>
  <p class="abs about-text">ut perspiciatis unde omnis iste natus error sit voluptatem accusantium doloremque laudantium, totam rem aperiam, eaque ipsa quae ab illo inventore veritatis et quasi architecto beatae vitae dicconsequuntur magni dolores eos qui ratioula dolor sit amet, consectetam quaerat voluptatem. Ut enim ad minima veniam, quis nostrum exercitationem ullam corporis suscipit laboriosam, nisi ut aliquid ex ea commodi consequatur? Quis autem vel eum iure reprehenderit qui in ea voluptate velit esse quam nihil molestiae consequatur, vel illum qui dolorem eum</p>
  <div class="abs read-more">Read More &gt;&gt;</div>
</section>

<h2 class="abs section-title" style="top:879px">Latest Events</h2>
<p class="abs section-sub" style="top:911px">Nemo enim ipsam voluptatem quia voluptas sit aspernatur aut odit aut fugit, sed quia consequuntur</p>

<div class="abs event left" style="left:78px;top:963px">
  <div class="event-title">Life Coaching/Counselling</div>
  <div class="event-meta">8.00 am - 5.00 <svg width="8" height="8" viewBox="0 0 8 8"><circle cx="4" cy="4" r="3.2" fill="none" stroke="#ef5f3c" stroke-width="1.1"/><path d="M4 2v2h1.5" fill="none" stroke="#ef5f3c"/></svg></div>
  <div class="event-meta">Street Name, City Name <svg width="7" height="9" viewBox="0 0 7 9"><path d="M3.5 9C1 5.5 0 4.5 0 3.3a3.5 3.5 0 0 1 7 0C7 4.5 6 5.5 3.5 9z" fill="#ef5f3c"/><circle cx="3.5" cy="3.3" r="1.2" fill="#fff"/></svg></div>
</div>
<div class="abs date" style="left:238px;top:962px"><span>02</span><b>DEC</b></div>

<div class="abs event left" style="left:78px;top:1051px">
  <div class="event-title">Personal training</div>
  <div class="event-meta">8.00 am - 5.00 <svg width="8" height="8" viewBox="0 0 8 8"><circle cx="4" cy="4" r="3.2" fill="none" stroke="#ef5f3c" stroke-width="1.1"/><path d="M4 2v2h1.5" fill="none" stroke="#ef5f3c"/></svg></div>
  <div class="event-meta">Street Name, City Name <svg width="7" height="9" viewBox="0 0 7 9"><path d="M3.5 9C1 5.5 0 4.5 0 3.3a3.5 3.5 0 0 1 7 0C7 4.5 6 5.5 3.5 9z" fill="#ef5f3c"/><circle cx="3.5" cy="3.3" r="1.2" fill="#fff"/></svg></div>
</div>
<div class="abs date" style="left:238px;top:1050px"><span>02</span><b>DEC</b></div>

<div class="abs center-brand">
  <span class="brand-dot"></span>
  <div class="brand-name">FernPath</div>
  <div class="brand-tag">A dash of Glow</div>
</div>

<div class="abs date" style="left:476px;top:962px"><span>02</span><b>DEC</b></div>
<div class="abs event" style="left:541px;top:963px;width:160px">
  <div class="event-title">Massage and Sports Massage</div>
  <div class="event-meta"><svg width="8" height="8" viewBox="0 0 8 8"><circle cx="4" cy="4" r="3.2" fill="none" stroke="#ef5f3c" stroke-width="1.1"/><path d="M4 2v2h1.5" fill="none" stroke="#ef5f3c"/></svg> December 02 @ 8.00 am - 5.00</div>
  <div class="event-meta"><svg width="7" height="9" viewBox="0 0 7 9"><path d="M3.5 9C1 5.5 0 4.5 0 3.3a3.5 3.5 0 0 1 7 0C7 4.5 6 5.5 3.5 9z" fill="#ef5f3c"/><circle cx="3.5" cy="3.3" r="1.2" fill="#fff"/></svg> Street Name, City Name</div>
</div>

<div class="abs date" style="left:476px;top:1050px"><span>02</span><b>DEC</b></div>
<div class="abs event" style="left:541px;top:1051px;width:160px">
  <div class="event-title">Life Coaching/Counselling</div>
  <div class="event-meta"><svg width="8" height="8" viewBox="0 0 8 8"><circle cx="4" cy="4" r="3.2" fill="none" stroke="#ef5f3c" stroke-width="1.1"/><path d="M4 2v2h1.5" fill="none" stroke="#ef5f3c"/></svg> December 02 @ 8.00 am - 5.00</div>
  <div class="event-meta"><svg width="7" height="9" viewBox="0 0 7 9"><path d="M3.5 9C1 5.5 0 4.5 0 3.3a3.5 3.5 0 0 1 7 0C7 4.5 6 5.5 3.5 9z" fill="#ef5f3c"/><circle cx="3.5" cy="3.3" r="1.2" fill="#fff"/></svg> Street Name, City Name</div>
</div>

<footer>
  <div class="abs footer"></div>
  <div class="abs footer-links">Home &nbsp;| &nbsp;About Us &nbsp;| &nbsp;Services &nbsp;| &nbsp;Our Aim &nbsp;| &nbsp;Testimonials &nbsp;| &nbsp;Contacts</div>
  <div class="abs footer-copy">© 2015. FernPath.com All rights reserved</div>
  <div class="abs social"><i></i><i></i><i></i><i></i><i></i></div>
</footer>
</body>
</html>
```